Gobal construction supply company needs new business card design

I need a business card design for my global supply company using an existing logo. i will be looking to print these on rounded corner cards with the black background version of my logo on the back. on the front white background, my logo again and my simple details.

```html
<!DOCTYPE html>
<html lang="en">
<head>
<meta charset="utf-8">
<title>Meridian Supply Group – Business Card</title>
<link rel="stylesheet" href="https://fonts.googleapis.com/css2?family=Montserrat:wght@600&family=Work+Sans:wght@400;500&display=swap">
<style>
  :root {
    --backdrop: #1c1c1d;
    --card: #262627;
    --card-edge: #303031;
    --ink: #f2f2f2;
    --silver: #bdbdbd;
    --accent: #e0202a;
  }
  * { box-sizing: border-box; margin: 0; padding: 0; }
  html, body {
    width: 1200px; height: 900px; overflow: hidden;
    background: var(--backdrop);
  }
  .canvas { position: relative; width: 1200px; height: 900px; }
  .card {
    position: absolute; left: 250px; width: 700px; height: 400px;
    border-radius: 18px;
    background: linear-gradient(135deg, var(--card) 0%, #2c2c2d 60%, var(--card-edge) 100%);
  }
  .card--back { top: 35px; }
  .card--front { top: 465px; }

  /* back */
  .brand-lockup {
    position: absolute; inset: 0;
    display: flex; align-items: center; justify-content: center;
  }
  .brand-lockup__name {
    font-family: "Montserrat", sans-serif; font-weight: 600;
    font-size: 34px; letter-spacing: 1px; text-transform: uppercase;
    color: var(--silver);
  }

  /* front */
  .front-brand {
    position: absolute; left: 56px; top: 48px;
    font-family: "Montserrat", sans-serif; font-weight: 600;
    font-size: 22px; letter-spacing: 0.5px; text-transform: uppercase;
    color: var(--ink);
  }
  .person { position: absolute; left: 56px; top: 118px; }
  .person__name {
    font-family: "Montserrat", sans-serif; font-weight: 600;
    font-size: 30px; text-transform: uppercase; color: var(--accent);
    line-height: 1.1;
  }
  .person__role {
    font-family: "Work Sans", sans-serif; font-size: 18px; color: var(--ink);
    margin-top: 2px;
  }
  .address {
    position: absolute; left: 56px; top: 205px;
    font-family: "Work Sans", sans-serif; font-style: normal;
    font-size: 18px; line-height: 1.4;
    color: var(--ink); letter-spacing: 0.5px;
  }
  .contact {
    position: absolute; left: 44px; top: 278px; list-style: none;
    font-family: "Work Sans", sans-serif; font-size: 18px; line-height: 1.45;
    color: var(--ink); letter-spacing: 0.5px;
  }
  .contact__item { display: flex; align-items: center; gap: 10px; }
  .contact__icon { width: 12px; height: 12px; flex: none; }

  .front-mark {
    position: absolute; right: 56px; top: 150px;
    font-family: "Montserrat", sans-serif; font-weight: 600;
    font-size: 40px; text-transform: uppercase; color: var(--silver);
  }
</style>
</head>
<body>
<main class="canvas">

  <section class="card card--back" aria-label="Card back">
    <div class="brand-lockup">
      <span class="brand-lockup__name">Meridian Supply Group</span>
    </div>
  </section>

  <section class="card card--front" aria-label="Card front">
    <div class="front-brand">Meridian Supply Group</div>

    <div class="person">
      <div class="person__name">Daniel Rourke</div>
      <div class="person__role">Director</div>
    </div>

    <address class="address">
      48 Harbour Road Box<br>2710, Lakeview, AB
    </address>

    <ul class="contact">
      <li class="contact__item">
        <svg class="contact__icon" viewBox="0 0 12 12" aria-hidden="true">
          <path d="M2.5 1 L4.5 1 L5 3.5 L3.8 4.4 Q5 7 7.6 8.2 L8.5 7 L11 7.5 L11 9.5 Q10 11 8.5 11 Q1 9 1 2.5 Q1 1 2.5 1 Z" fill="var(--accent)"/>
        </svg>
        <span>403-555-0182</span>
      </li>
      <li class="contact__item">
        <svg class="contact__icon" viewBox="0 0 12 12" aria-hidden="true">
          <rect x="1" y="2.5" width="10" height="7" fill="none" stroke="var(--accent)" stroke-width="1.2"/>
          <path d="M1 2.5 L6 6.5 L11 2.5" fill="none" stroke="var(--accent)" stroke-width="1.2"/>
        </svg>
        <span>info@meridiansupply.com</span>
      </li>
      <li class="contact__item">
        <svg class="contact__icon" viewBox="0 0 12 12" aria-hidden="true">
          <circle cx="6" cy="6" r="5" fill="none" stroke="var(--accent)" stroke-width="1.2"/>
          <ellipse cx="6" cy="6" rx="2.2" ry="5" fill="none" stroke="var(--accent)" stroke-width="1"/>
          <path d="M1 6 H11" stroke="var(--accent)" stroke-width="1"/>
        </svg>
        <span>www.meridiansupply.com</span>
      </li>
    </ul>

    <div class="front-mark">Meridian</div>
  </section>

</main>
</body>
</html>
```